Wellbrook Talking Therapies Hub Swindon

We need a design for magazine advert, ideally high resolution to advertise our counselling centre. we would like this to include a photo of two people talking, as if in a counselling session. See our logo and colour range on our website. www.wbtth-swindon.co.uk
The photo should not include cups of coffee, clipboards, desks, people touching. it needs to be two people in armchairs sympathetically listening and looking at each other.
The font type is Great Vibes on the logo. Our design should communicate a centre of excellence delivering high quality, professional services in stylishly furnished surroundings.

Hello Everyone We have had a number of designs that look quite promising but are missing the brief. Can I reiterate that we need a photograph of 2 people seated talking to each other in a sincere way. There shouldn't be office chairs but comfortable chairs. There should be no physical contact. There should be no clipboards.Thank you very muchHeather Added Sunday, March 12, 2017

Target Market(s)

people seeking counselling and psychotherapy

Font styles to use
Other font styles liked:
• Great Vibes as in our logo for some of the print. See attached file.

Requirements
Must have
• good photograph
• Two high res Pixavend photos:
• https://pixavend-files.example-cdn.net/download?id=a81kd93jf02mdl47xq
• https://pixavend-files.example-cdn.net/download?id=z57pw20ne84bvc13ty
Nice to have
• Watermark in keeping with our logo.
Should not have
• Darkness

```html
<!DOCTYPE html>
<html lang="en">
<head>
<meta charset="utf-8">
<title>Wellbrook Talking Therapies Hub – Magazine Advert</title>
<link rel="stylesheet" href="https://fonts.googleapis.com/css2?family=Great+Vibes&family=Montserrat:wght@400;500;600&display=swap">
<style>
  :root {
    --page-bg: #e6e6e6;
    --cream: #f2ecdd;
    --sage: #a9bd8c;
    --leaf-green: #8fae5f;
    --olive-text: #7f9a2c;
    --espresso: #3d3230;
    --ink: #2e2624;
    --white: #ffffff;
  }
  * { margin: 0; padding: 0; box-sizing: border-box; }
  html, body {
    width: 1200px; height: 1200px; overflow: hidden;
    background: var(--page-bg);
  }
  .advert {
    position: absolute; left: 210px; top: 48px;
    width: 780px; height: 1104px;
    background: var(--white);
    box-shadow: 0 12px 40px rgba(0,0,0,0.18);
    overflow: hidden;
    font-family: "Montserrat", sans-serif;
  }
  .advert__shapes { position: absolute; inset: 0; width: 780px; height: 1104px; }
  .headline {
    position: absolute; left: 0; width: 780px; top: 488px;
    font-family: "Great Vibes", cursive; font-weight: 400;
    color: var(--ink); font-size: 54px; line-height: 60px;
    text-align: center;
  }
  .headline span { display: block; }
  .intro {
    position: absolute; left: 162px; top: 664px; width: 320px;
    font-size: 16.5px; line-height: 23px; color: var(--ink);
  }
  .intro strong { color: var(--olive-text); font-weight: 600; }
  .contact {
    position: absolute; left: 63px; top: 912px; width: 290px;
    color: var(--white);
  }
  .contact__hours { font-size: 14.5px; line-height: 17px; }
  .contact__phone { font-size: 31px; line-height: 38px; color: var(--sage); font-weight: 400; margin-top: 2px; }
  .contact__address { font-size: 14px; line-height: 17px; margin-top: 8px; }
  .contact__web { font-size: 15px; font-weight: 600; margin-top: 16px; }
  .brand {
    position: absolute; left: 380px; top: 900px; width: 390px;
    text-align: center;
  }
  .brand__dot {
    display: block; width: 44px; height: 44px; margin: 0 auto 14px;
    border-radius: 50%; background: var(--leaf-green);
  }
  .brand__name {
    font-family: "Great Vibes", cursive; font-weight: 400;
    font-size: 40px; line-height: 44px; color: var(--ink);
  }
</style>
</head>
<body>
  <article class="advert">
    <svg class="advert__shapes" viewBox="0 0 780 1104" xmlns="http://www.w3.org/2000/svg">
      <defs>
        <linearGradient id="heroTones" x1="0" y1="0" x2="1" y2="0.4">
          <stop offset="0" stop-color="#4a3a2f"/>
          <stop offset="0.45" stop-color="#9c8570"/>
          <stop offset="1" stop-color="#c9cdbf"/>
        </linearGradient>
        <linearGradient id="sessionTones" x1="0" y1="0" x2="1" y2="0">
          <stop offset="0" stop-color="#e9e7e6"/>
          <stop offset="0.5" stop-color="#d9c2bc"/>
          <stop offset="1" stop-color="#cfe0dc"/>
        </linearGradient>
      </defs>
      <rect class="hero-photo" x="0" y="0" width="780" height="660" fill="url(#heroTones)" role="img" aria-label="Photo of a thoughtful woman with eyes closed and hands clasped near her face, soft woodland background"/>
      <path class="accent-band" d="M0,548 C150,458 300,458 420,450 C560,440 700,390 780,240 L780,1104 L0,1104 Z" fill="var(--sage)"/>
      <path class="cream-wave" d="M0,560 C150,470 300,470 420,462 C560,452 700,405 780,262 L780,1104 L0,1104 Z" fill="var(--cream)"/>
      <path class="session-photo" d="M430,835 C470,740 560,680 640,650 C700,630 750,620 780,612 L780,720 C700,780 560,830 430,835 Z" fill="url(#sessionTones)" role="img" aria-label="Photo of a counsellor and a client seated in a bright consulting room, smiling"/>
      <path class="contact-panel" d="M0,860 C100,832 250,826 420,830 C360,900 330,980 320,1104 L0,1104 Z" fill="var(--espresso)"/>
      <path class="brand-panel" d="M420,830 C560,830 700,780 780,720 L780,1104 L320,1104 C330,980 360,900 420,830 Z" fill="var(--white)"/>
    </svg>

    <h1 class="headline">
      <span>Confidential Therapeutic Services</span>
      <span>in the Heart of Old Town</span>
    </h1>

    <p class="intro">We have over <strong>30 carefully selected, qualified and professional therapists</strong> offering a range of services to help individuals, families and couples.</p>

    <div class="contact">
      <p class="contact__hours">Appointments available<br>throughout the day and evening</p>
      <p class="contact__phone">01632 960418</p>
      <p class="contact__address">14 Elmcroft Lane, Old Town,<br>Swindon SN9 2QT</p>
      <p class="contact__web">www.wbtth-swindon.co.uk</p>
    </div>

    <div class="brand">
      <span class="brand__dot"></span>
      <p class="brand__name">Wellbrook Talking Therapies Hub</p>
    </div>
  </article>
</body>
</html>
```